Glimmora.ca Website Build For costume embellishment service

Design a website to promote our business.
Costume embellishing services for Artistic Swimming, Dance, Skating, Gymnastics etc.
We add sparkle to costumes using Kelvarne and Lumetta crystals to plain costumes that our customers provide. We also sell new costumes already decorated, Lastly we specialize in reimagining costumes to make them look like new.
We would like samples of our work to be displayed in pictures and video.
We need an information about our services page as well as a contact us page. We have a logo for Glimmora which is pink. We like a modern aesthetic as well as bright colours. We are hoping to promote our services worldwide but a big push for Canada. We need to convey that we are Canadian. We would like help with writing copy as well.
We currently have a cartwell webpage glimmora.ca but would like to shut down the cartwell site as we don't need the payment service. In the new website we will promote payment by PayRoam or transfer.
A copy of our logo is attached.

Target Market(s)

Athletes and Dancers under 18 years old and parents

Industry/Entity Type

costume embellishment service

Coding

Coded - Design and coding required

Number of Pages Required

4 page

Font styles to use
Sans Serif
Other font styles liked:
• match to the logo for titles

Colors
E54698
E96AAD
F1A4CE
F9D9EA
FCEFF6

Requirements
Must have
• Photos and video upload capability there will be allot of before and after pictures as well as unclose videos.
Nice to have
• modern look I like the look of this website http://www.bramblecloset-example.com
Should not have
• not busy looking

```html
<!DOCTYPE html>
<html lang="en">
<head>
<meta charset="utf-8">
<title>Glimmora — Costume Embellishing</title>
<link href="https://fonts.googleapis.com/css2?family=Montserrat:wght@300;400;500;700;800&family=Kaushan+Script&display=swap" rel="stylesheet">
<style>
:root{
  --pink:#d6338f;
  --hero:#d53e9c;
  --hero-deep:#c92e8e;
  --footer:#bb1580;
  --white:#ffffff;
  --ink:#4a4a4a;
  --line:rgba(255,255,255,.75);
}
*{margin:0;padding:0;box-sizing:border-box}
html,body{width:1200px;height:2561px;overflow:hidden;background:#fff}
body{position:relative;font-family:'Montserrat',sans-serif;color:var(--ink)}
.abs{position:absolute}

/* hero */
.hero{left:0;top:0;width:1200px;height:697px;background:linear-gradient(90deg,#d84ba2 0%,var(--hero) 45%,#d04ba0 100%)}
.hero-panel{background:rgba(255,255,255,.08)}
.contact-top{top:80px;font-size:16px;color:var(--white);display:flex;align-items:center;gap:12px}
.brand{left:490px;top:60px;width:222px;text-align:center;color:var(--white);font-size:34px;font-weight:300;letter-spacing:1px;display:flex;align-items:center;justify-content:center;gap:10px}
.brand-mark{width:12px;height:12px;background:var(--white)}
.nav-rule{left:111px;width:978px;height:1px;background:var(--line)}
.nav{left:111px;top:166px;width:978px;height:52px;display:flex;justify-content:center;align-items:center;gap:54px;font-size:15px;color:var(--white);letter-spacing:.3px}
.hero-title{left:108px;top:318px;font-family:'Kaushan Script',cursive;font-size:104px;color:var(--white);line-height:1.2}
.hero-sub{left:111px;top:496px;font-size:16px;color:var(--white)}
.btn-outline{left:110px;top:540px;width:174px;height:46px;border:2px solid var(--white);border-radius:24px;color:var(--white);font-size:15px;display:flex;align-items:center;justify-content:center}
.hero-athlete{left:705px;top:258px;width:236px;height:508px;border-radius:90px 90px 30px 30px;background:linear-gradient(180deg,#2a2350 0%,#e6b8a0 55%,#e8c2ac 100%)}

/* disciplines */
.tile{top:812px;width:236px;height:338px}
.tile-label{top:1160px;font-size:22px;color:var(--pink);font-weight:400;letter-spacing:.5px}

/* before after */
.before{left:0;top:1258px;width:598px;height:495px;background:radial-gradient(ellipse at 50% 45%,#4a3530 0%,#1a0f0d 60%,#0f0908 100%)}
.after{left:598px;top:1258px;width:602px;height:495px;background:linear-gradient(180deg,#c07a4a 0%,#e0a060 35%,#6b4030 70%,#1e1715 100%)}
.ba-label{top:1700px;font-size:22px;font-weight:800;letter-spacing:.5px}

/* about */
.about-photo-a{left:111px;top:1840px;width:458px;height:365px;background:linear-gradient(120deg,#f1e6e4 0%,#d8a4a8 50%,#f4ece8 100%)}
.about-photo-b{left:253px;top:2022px;width:348px;height:260px;background:linear-gradient(160deg,#101a2e 0%,#1e3f7a 55%,#0d1526 100%)}
.eyebrow{left:656px;top:1885px;font-size:16px;color:var(--ink)}
.about-title{left:656px;top:1908px;font-family:'Kaushan Script',cursive;font-size:54px;color:var(--pink);line-height:1.2}
.about-copy{left:656px;top:2002px;width:435px;font-size:13px;line-height:19px;color:#555}
.about-copy p{margin-bottom:18px}
.btn-solid{left:656px;top:2190px;width:171px;height:43px;border-radius:22px;background:var(--pink);color:var(--white);font-size:16px;display:flex;align-items:center;justify-content:center}

/* footer */
.footer{left:0;top:2368px;width:1200px;height:193px;background:var(--footer)}
.footer-brand{left:111px;top:2440px;color:var(--white);font-size:38px;font-weight:300;display:flex;align-items:center;gap:12px}
.footer-line{right:112px;font-size:13px;font-weight:700;color:var(--white);display:flex;align-items:center;gap:10px;letter-spacing:.3px}
.footer-rule{left:424px;top:2446px;width:664px;height:1px;background:var(--line)}
.copyright{right:112px;top:2504px;font-size:12px;color:var(--white)}
</style>
</head>
<body>

<section class="abs hero" aria-label="Hero">
  <div class="abs hero-panel" style="left:400px;top:0;width:400px;height:697px"></div>
  <div class="abs hero-panel" style="left:800px;top:0;width:400px;height:350px"></div>
</section>

<div class="abs contact-top" style="left:111px">
  <svg width="16" height="12" viewBox="0 0 16 12"><rect x="0" y="0" width="16" height="12" rx="1" fill="#fff"/><path d="M0 1 L8 7 L16 1" stroke="#d53e9c" stroke-width="1.5" fill="none"/></svg>
  info@glimmora.ca
</div>
<div class="abs brand"><span class="brand-mark"></span>Glimmora</div>
<div class="abs contact-top" style="right:112px">
  <svg width="16" height="16" viewBox="0 0 24 24"><path fill="#fff" d="M6.6 10.8a15.1 15.1 0 0 0 6.6 6.6l2.2-2.2a1 1 0 0 1 1-.25 11.4 11.4 0 0 0 3.6.57 1 1 0 0 1 1 1V20a1 1 0 0 1-1 1A17 17 0 0 1 3 4a1 1 0 0 1 1-1h3.5a1 1 0 0 1 1 1c0 1.25.2 2.45.57 3.57a1 1 0 0 1-.25 1z"/></svg>
  555-014-2278
</div>

<div class="abs nav-rule" style="top:165px"></div>
<nav class="abs nav"><span>HOME</span><span>ABOUT US</span><span>SERVICES</span><span>GALLERY</span><span>CONTACT US</span></nav>
<div class="abs nav-rule" style="top:218px"></div>

<h1 class="abs hero-title">Glimmora</h1>
<p class="abs hero-sub">We provide Costume embellishing services for Artistic.</p>
<a class="abs btn-outline">Learn More</a>
<div class="abs hero-athlete" role="img" aria-label="Photo of a gymnast in a sparkling leotard holding a standing split"></div>

<div class="abs tile" style="left:111px;background:linear-gradient(160deg,#2fae8e,#c8282e 70%,#e0a080)" role="img" aria-label="Photo of a swimmer in a red swimsuit"></div>
<div class="abs tile" style="left:359px;background:linear-gradient(160deg,#f2f0ec,#ee6a2a 70%,#f4f0ea)" role="img" aria-label="Photo of a dancer in an orange embellished costume"></div>
<div class="abs tile" style="left:607px;background:linear-gradient(180deg,#9a9a9a,#5b4ca0 45%,#8a8a8a)" role="img" aria-label="Photo of a skater jumping on a skateboard"></div>
<div class="abs tile" style="left:855px;background:linear-gradient(160deg,#e6e4e2,#d0201e 55%,#eceae8)" role="img" aria-label="Photo of a gymnast in a red costume with a mask"></div>
<div class="abs tile-label" style="left:111px">Swimming</div>
<div class="abs tile-label" style="left:359px">Dance</div>
<div class="abs tile-label" style="left:607px">Skating</div>
<div class="abs tile-label" style="left:855px">Gymnastics</div>

<div class="abs before" role="img" aria-label="Photo of a dancer in a plain costume before embellishment"></div>
<div class="abs after" role="img" aria-label="Photo of a dancer in a bright yellow embellished costume at sunset"></div>
<div class="abs ba-label" style="left:110px;color:var(--white)">BEFORE</div>
<div class="abs ba-label" style="left:637px;color:var(--pink)">AFTER</div>

<div class="abs about-photo-a" role="img" aria-label="Photo of the costume designer in her studio"></div>
<div class="abs about-photo-b" role="img" aria-label="Photo of two dancers in blue embellished costumes"></div>
<div class="abs eyebrow">About Us</div>
<h2 class="abs about-title">Glimmora</h2>
<div class="abs about-copy">
  <p>Dazzling competition suits and costumes for all sports and events.</p>
  <p>Create a Dazzling new costume or restyle an existing favourite... no job is too big or too small.&nbsp; Artistic Swimming, Dance, Gymnastics and Skating!</p>
  <p>Our master costume applique designer will work closely with you to fully understand your needs before starting any project.&nbsp; Your satisfaction is our ultimate goal.</p>
</div>
<a class="abs btn-solid">Learn More</a>

<footer class="abs footer" aria-label="Footer"></footer>
<div class="abs footer-brand"><span class="brand-mark"></span>Glimmora</div>
<div class="abs footer-line" style="top:2413px">
  <svg width="14" height="14" viewBox="0 0 24 24"><path fill="#fff" d="M6.6 10.8a15.1 15.1 0 0 0 6.6 6.6l2.2-2.2a1 1 0 0 1 1-.25 11.4 11.4 0 0 0 3.6.57 1 1 0 0 1 1 1V20a1 1 0 0 1-1 1A17 17 0 0 1 3 4a1 1 0 0 1 1-1h3.5a1 1 0 0 1 1 1c0 1.25.2 2.45.57 3.57a1 1 0 0 1-.25 1z"/></svg>
  <span>555-014-2278</span><span style="margin:0 10px">|</span>
  <svg width="14" height="11" viewBox="0 0 16 12"><rect width="16" height="12" rx="1" fill="#fff"/><path d="M0 1 L8 7 L16 1" stroke="#bb1580" stroke-width="1.5" fill="none"/></svg>
  <span>INFO@GLIMMORA.CA</span>
</div>
<div class="abs footer-rule"></div>
<div class="abs footer-line" style="top:2463px">
  <svg width="12" height="15" viewBox="0 0 12 16"><path fill="#fff" d="M6 0a6 6 0 0 0-6 6c0 4.5 6 10 6 10s6-5.5 6-10a6 6 0 0 0-6-6zm0 8.2A2.2 2.2 0 1 1 6 3.8a2.2 2.2 0 0 1 0 4.4z"/></svg>
  <span style="margin-left:8px">418 RUE LAVANDE, QUEBEC, G1R 2K4, CANADA.</span>
</div>
<div class="abs copyright">© Copyright 2021 Glimmora .</div>

</body>
</html>
```